Counseling Practice Business Card

I need a professional looking business card incorporating my new logo that was just completed. Card needs to incorporate my name and title, description of my specialty, my address, my phone number, my fax number, my email and my website URL. I need to be able to choose design on/with different paper colors and textures.
I do not have a lot of business card ideas so I am open to anything but I want bold,sharp, clear card without additional designs other than my logo (see attached file info). I am open to different color backgrounds or paper colors including black. I do not like traditional brackets around area codes in phone number or dashes between numbers in phone number. Am open to other ways of presenting including periods between numbers as appropriate. I do not know enough to know what I like yet but I want card to coordinate and work together with my logo. My practice emphasizes natural mental health interventions so any use of color (with background paper color or the blue and green in my logo) that elicits nature is nice. In addition to black, any natural brown or wood looking background might be desirable also. Most of the offerings so far look very similar and boring.

Target Market(s)

Potential therapy clients and other professionals

Contact Information for Business Card

Card information:
Gerald M. Whitcombe, Ph.D.
Licensed Clinical Psychologist
Integrative Health Coach
4812 Marlowe Ridge Blvd SE
Suite 310
Duluth, GA 30096
(770) 415-2983 phone
(770) 581-4096 fax
drgeraldwhitcombe@quillmarsh.net
brightfernwellness.net

Font styles to use
Serif
Sans Serif
Other font styles liked:
• anything that you think looks crisp, clear and easily readable

Requirements
Must have
• Any color used should coordinate with my logo design (see attached files).
• Card should be printed horizontally so top and bottom are longest sides of rectangle.
• Background color or paper color should complement and highlight logo. Do not like a white background. black, grey, brown or any color my logo would blend well with.
Nice to have
• I would like designer to utilize color to highlight letters/name or phone-fax-web symbols.
• Bottom edge of card could be highlighted if appropriate to an idea.
Should not have
• I would NOT want the card to have a pure white background at all.
• No clear cards.
• Cards should be oriented with long sides on bottom and top, NOT sides. DO NOT LIKE THIS THIN TALL ORIENTATION.

```html
<!DOCTYPE html>
<html lang="en">
<head>
<meta charset="utf-8">
<title>Brightfern Wellness – Business Card</title>
<link rel="stylesheet" href="https://fonts.googleapis.com/css2?family=Open+Sans:wght@400;600&display=swap">
<style>
  :root {
    --stage: #2b2b2b;
    --card-light: #efefef;
    --brand-blue: #2673b8;
    --label-blue: #2a6fb5;
    --name-green: #1f6b35;
    --ink: #333333;
    --rule: #555555;
    --white: #ffffff;
  }
  * { margin: 0; padding: 0; box-sizing: border-box; }
  html, body {
    width: 1200px; height: 1200px; overflow: hidden;
    background: var(--stage);
    font-family: "Open Sans", Arial, sans-serif;
  }
  .card {
    position: absolute;
    left: 250px;
    width: 700px; height: 400px;
  }
  .card--front { top: 170px; background: var(--card-light); color: var(--ink); display: flex; }
  .card--back {
    top: 630px; background: var(--brand-blue); color: var(--white);
    display: flex; align-items: center; justify-content: center;
  }

  .brand {
    display: flex; align-items: center; justify-content: center; gap: 14px;
    font-weight: 600; font-size: 34px; line-height: 1.15;
  }
  .brand__dot { width: 20px; height: 20px; border-radius: 50%; flex: none; }
  .brand__name { text-align: left; }
  .card--front .brand { color: var(--label-blue); }
  .card--front .brand__dot { background: var(--label-blue); }
  .card--back .brand { color: var(--white); }
  .card--back .brand__dot { background: var(--white); }

  .card__brand-side {
    width: 300px; display: flex; align-items: center; justify-content: center;
  }
  .card__divider { width: 1px; background: var(--rule); margin: 60px 0; }
  .card__details {
    flex: 1; display: flex; flex-direction: column; align-items: center; justify-content: center;
    text-align: center; padding: 0 20px;
  }

  .holder__name { font-size: 19px; font-weight: 600; color: var(--label-blue); letter-spacing: 0.2px; }
  .holder__name .surname { color: var(--name-green); }
  .holder__role { font-size: 16px; line-height: 21px; margin-top: 2px; }

  .rule { width: 222px; height: 1px; background: var(--rule); margin: 12px 0; }

  .contact { list-style: none; font-size: 16px; line-height: 21.5px; }
  .contact .label { color: var(--label-blue); }

  .address { font-size: 16px; line-height: 21px; font-style: normal; }
</style>
</head>
<body>
  <section class="card card--front" aria-label="Business card front">
    <div class="card__brand-side">
      <div class="brand">
        <span class="brand__dot"></span>
        <span class="brand__name">Brightfern<br>Wellness</span>
      </div>
    </div>

    <div class="card__divider"></div>

    <div class="card__details">
      <div class="holder">
        <p class="holder__name">GERALD M. <span class="surname">WHITCOMBE,</span> PH.D.</p>
        <p class="holder__role">Licensed Clinical Psychologist /<br>Integrative Health Coach</p>
      </div>

      <div class="rule"></div>

      <ul class="contact">
        <li><span class="label">P:</span> 770. 415.2983</li>
        <li><span class="label">F:</span> 770. 581.4096</li>
        <li><span class="label">E:</span> drgeraldwhitcombe@quillmarsh.net</li>
        <li><span class="label">W:</span> www.brightfernwellness.net</li>
      </ul>

      <div class="rule"></div>

      <address class="address">4812 Marlowe Ridge Blvd SE<br>Suite 310 Duluth, GA 30096</address>
    </div>
  </section>

  <section class="card card--back" aria-label="Business card back">
    <div class="brand">
      <span class="brand__dot"></span>
      <span class="brand__name">Brightfern<br>Wellness</span>
    </div>
  </section>
</body>
</html>
```